Healthy lifestyle Influencer business card

I need your creativity to have a business card that I can leave in all the restaurants, hotels and spas I visit to inform them that I am an influencer specializing in the wellness sector and that I will write a review about them. You can use my instagram photos Lunavita27 or on my website www.piattileggeriorto.it. I would like my business card to impress with its creativity! thank you very much!

Contact Information for Business Card

siteweb, instagram, phone number

Font styles to use
Decorative
Script

Colors
0094D4
00A9DD
6FCCEA
C7EBF8
E9F6FB
59FF00
82FF00
B8FF75
E3FFCB
F4FFEA
FFC000
F8CF3A
FAE287
FDF2CF
FEFAEE
F0912C
F2A743
F7CA91
FBE8D2
FDF5EE
EE7325
F08F49
F5BC92
FAE3D3
FDF4ED
EB3D1F
EC4F4E
F09395
F8D3D4
FCEDEE
E54698
E96AAD
F1A4CE
F9D9EA
FCEFF6

Requirements
Nice to have
• creativity

```html
<!DOCTYPE html>
<html lang="it">
<head>
<meta charset="utf-8">
<title>Luna Vita Cucina – Biglietto da visita</title>
<link rel="stylesheet" href="https://fonts.googleapis.com/css2?family=Great+Vibes&family=Roboto:wght@300;400&display=swap">
<style>
  :root {
    --backdrop: #2a2a2b;
    --card-front: #97b8ae;
    --card-back: #90b1a7;
    --ink-dark: #4b4b4d;
    --ink-light: #f3f6f4;
    --ink-soft: #e6eeeb;
    --dot: #c94a5a;
  }
  html, body {
    margin: 0;
    padding: 0;
    width: 1138px;
    height: 1200px;
    overflow: hidden;
    background: var(--backdrop);
    font-family: "Roboto", sans-serif;
  }
  .canvas {
    position: relative;
    width: 1138px;
    height: 1200px;
  }
  .card {
    position: absolute;
    top: 273px;
    width: 375px;
    height: 620px;
    border-radius: 16px;
    overflow: hidden;
  }
  .card--front { left: 158px; background: var(--card-front); }
  .card--back  { left: 578px; background: var(--card-back); }

  .brand-vertical {
    position: absolute;
    left: 187px;
    top: 295px;
    width: 420px;
    transform: translate(-50%, -50%) rotate(-90deg);
    text-align: center;
    color: var(--ink-dark);
  }
  .brand-name {
    font-family: "Roboto", sans-serif;
    font-weight: 300;
    font-size: 36px;
    letter-spacing: 1px;
    line-height: 1.1;
  }
  .brand-tagline {
    font-family: "Roboto", sans-serif;
    font-weight: 400;
    font-size: 16px;
    margin-top: 8px;
  }

  .social {
    position: absolute;
    left: 0;
    right: 0;
    bottom: 36px;
    display: flex;
    justify-content: center;
    align-items: center;
    gap: 10px;
    font-size: 16px;
    font-weight: 400;
  }
  .card--front .social { color: var(--ink-dark); }
  .card--back .social { color: var(--ink-light); }
  .social-dot {
    width: 14px;
    height: 14px;
    border-radius: 50%;
    background: var(--dot);
  }

  .brand-block {
    position: absolute;
    top: 132px;
    left: 0;
    right: 0;
    text-align: center;
    color: var(--ink-light);
  }

  .owner-name {
    position: absolute;
    top: 315px;
    left: 0;
    right: 0;
    text-align: center;
    font-family: "Great Vibes", cursive;
    font-size: 33px;
    color: var(--ink-light);
  }
  .contact-divider {
    position: absolute;
    top: 388px;
    left: 75px;
    width: 225px;
    height: 28px;
  }
  .contact-list {
    position: absolute;
    top: 433px;
    left: 0;
    right: 0;
    margin: 0;
    padding: 0;
    list-style: none;
    text-align: center;
    font-weight: 300;
    font-size: 15.5px;
    line-height: 24px;
    color: var(--ink-soft);
  }
</style>
</head>
<body>
<main class="canvas">

  <section class="card card--front" aria-label="Fronte del biglietto">
    <div class="brand-vertical">
      <div class="brand-name">Luna Vita Cucina</div>
      <div class="brand-tagline">Bene ogni giorno a tavola</div>
    </div>
    <div class="social">
      <span class="social-dot"></span>
      <span class="social-handle">@Lunavita27</span>
    </div>
  </section>

  <section class="card card--back" aria-label="Retro del biglietto">
    <div class="brand-block">
      <div class="brand-name">Luna Vita Cucina</div>
      <div class="brand-tagline">Bene ogni giorno a tavola</div>
    </div>

    <div class="owner-name">Chiara Bellini</div>

    <svg class="contact-divider" viewBox="0 0 225 28" aria-hidden="true">
      <g stroke="#eef3f1" fill="none" stroke-width="1.4">
        <line x1="0" y1="14" x2="62" y2="14"/>
        <line x1="163" y1="14" x2="225" y2="14"/>
        <circle cx="87" cy="14" r="11"/>
        <path d="M82 10c1-2 3-2 4 0l-1 2c1 2 2 3 4 4l2-1c2 1 2 3 0 4-4 1-10-5-9-9z" stroke-width="1.1"/>
        <circle cx="112.5" cy="14" r="11"/>
        <rect x="106" y="9.5" width="13" height="9" stroke-width="1.1"/>
        <path d="M106 9.5l6.5 5 6.5-5" stroke-width="1.1"/>
        <circle cx="138" cy="14" r="11"/>
        <circle cx="138" cy="14" r="6" stroke-width="1.1"/>
        <ellipse cx="138" cy="14" rx="2.5" ry="6" stroke-width="1"/>
        <line x1="132" y1="14" x2="144" y2="14" stroke-width="1"/>
      </g>
    </svg>

    <ul class="contact-list">
      <li>000-0000-0000</li>
      <li>info@piattileggeriorto.it</li>
      <li>www.piattileggeriorto.it</li>
    </ul>

    <div class="social">
      <span class="social-dot"></span>
      <span class="social-handle">@Lunavita27</span>
    </div>
  </section>

</main>
</body>
</html>
```